Creative, fresh business card design for Ripplecraft Facades

We need a fresh, creative business card design for Ripplecraft Facades. We are the manufacturer of Ripplecraft Facades in Australia. Wall panels are 2400 x 1200mm panels made from MDF and feature 3D patterns on the face of the panel. The colours to be used are green, silver/grey and white RGB
Red 187
Green 207
Blue 65.

An idea is to possibly use a watermark of one of our designs as a background (like on the "Grids" design on the left hand side of page 2 of our brochure).

Target Market(s)

Interior designers, architects, builders and home renovators

Industry/Entity Type

Business

Contact Information for Business Card

Details to go on the card are:
Our logo (attached),
Slogan: "Decorative panels for interiors and exteriors",
Contact name,
Position,
Mobile phone number,
Business address,
Business phone,
Business fax,
Website and
Email address.

I have attached a few images of our panels and our brochure for reference.

The colours of the business card should feature our logo colours which are: RGB
Red 187
Green 207
Blue 65

Requirements
Must have
• Very modern fonts and design. Some of the designs shown especially the "Prisms" design which is a popular design.
Nice to have
• Creative but simple design. Very contemporary.
Should not have
• Anything ornate or old fashioned.

```html
<!DOCTYPE html>
<html lang="en">
<head>
<meta charset="utf-8">
<title>Ripplecraft Facades — Business Card</title>
<link href="https://fonts.googleapis.com/css2?family=Quicksand:wght@400;500;600&display=swap" rel="stylesheet">
<style>
  :root {
    --stage: #d9d6d0;
    --card: #141414;
    --card-edge: #0a0a0a;
    --lime: #bbcf41;
    --silver: #b9b9b9;
    --text-grey: #a8a8a8;
    --white: #f2f2f2;
  }
  * { box-sizing: border-box; margin: 0; padding: 0; }
  html, body {
    width: 1200px; height: 1022px; overflow: hidden;
    background: var(--stage);
    font-family: "Quicksand", "Helvetica Neue", Arial, sans-serif;
  }
  .stage {
    width: 1200px; height: 1022px;
    display: flex; align-items: center; justify-content: center;
  }
  .card {
    position: relative;
    width: 920px; height: 526px;
    background: var(--card);
    border: 1px solid var(--card-edge);
    box-shadow: 0 18px 40px rgba(0,0,0,.35);
    overflow: hidden;
  }
  .card__texture {
    position: absolute; inset: 0;
    background: radial-gradient(ellipse at 40% 40%, #1f1f1f 0%, #151515 55%, #0e0e0e 100%);
  }
  .card__lines { position: absolute; inset: 0; }
  .brand {
    position: absolute; left: 34px; top: 262px; width: 180px;
  }
  .brand__mark {
    display: flex; align-items: center; gap: 10px;
  }
  .brand__square {
    width: 34px; height: 34px; background: var(--lime); flex: none;
  }
  .brand__name {
    color: var(--lime); font-weight: 600; font-size: 21px; line-height: 1.1;
  }
  .brand__slogan {
    margin-top: 14px;
    color: var(--text-grey); font-size: 12px; letter-spacing: 2px; line-height: 1.5;
  }
  .person {
    position: absolute; right: 70px; top: 150px; text-align: right;
  }
  .person__name {
    color: var(--lime); font-size: 34px; font-weight: 500; letter-spacing: 1px;
  }
  .person__role {
    position: absolute; right: 0; top: 60px;
    color: var(--text-grey); font-size: 16px; letter-spacing: 1px;
  }
  .address {
    position: absolute; right: 70px; top: 268px; text-align: right;
    color: var(--text-grey); font-size: 19px; line-height: 1.55; letter-spacing: 1px;
  }
  .contacts {
    position: absolute; left: 262px; top: 268px;
    list-style: none;
  }
  .contacts__item {
    display: flex; align-items: center; gap: 18px;
    color: var(--text-grey); font-size: 19px; letter-spacing: 1px; line-height: 1.75;
  }
  .contacts__icon { width: 16px; height: 16px; flex: none; }
</style>
</head>
<body>
<main class="stage">
  <article class="card">
    <div class="card__texture" role="img" aria-label="Subtle embossed ripple panel texture across the card background"></div>

    <svg class="card__lines" viewBox="0 0 920 526" aria-hidden="true">
      <g stroke="var(--lime)" stroke-width="2.5" fill="none">
        <polyline points="0,470 226,470 226,238 850,238 850,200"/>
      </g>
    </svg>

    <div class="brand">
      <div class="brand__mark">
        <span class="brand__square"></span>
        <span class="brand__name">Ripplecraft Facades</span>
      </div>
      <p class="brand__slogan">decorative panels for interiors &amp; landscapes</p>
    </div>

    <div class="person">
      <h1 class="person__name">Jonah Whitfield</h1>
      <p class="person__role">President</p>
    </div>

    <address class="address" style="font-style:normal">
      2710 Harbour Ridge rd<br>
      Westmere Bay, NSW 2187
    </address>

    <ul class="contacts">
      <li class="contacts__item">
        <svg class="contacts__icon" viewBox="0 0 16 16"><rect x="4" y="1" width="8" height="14" rx="1.5" fill="none" stroke="var(--lime)" stroke-width="1.6"/><rect x="7" y="12" width="2" height="1.4" fill="var(--lime)"/></svg>
        613. 405. 1187
      </li>
      <li class="contacts__item">
        <svg class="contacts__icon" viewBox="0 0 16 16"><path d="M3 2 L6 2 L7 5 L5.5 6.5 Q7 9.5 9.5 10.5 L11 9 L14 10 L14 13 Q8 14 4.5 10 Q1.5 6 3 2 Z" fill="var(--lime)"/></svg>
        613. 405. 2296
      </li>
      <li class="contacts__item">
        <svg class="contacts__icon" viewBox="0 0 16 16"><rect x="4" y="1" width="8" height="4" fill="var(--lime)"/><rect x="1" y="6" width="14" height="6" rx="1" fill="var(--lime)"/><rect x="4" y="10" width="8" height="5" fill="var(--lime)" stroke="var(--card)" stroke-width="1"/></svg>
        613. 405. 2297
      </li>
      <li class="contacts__item">
        <svg class="contacts__icon" viewBox="0 0 16 16"><rect x="1" y="3" width="14" height="10" fill="var(--lime)"/><polyline points="1,3 8,9 15,3" fill="none" stroke="var(--card)" stroke-width="1.3"/></svg>
        jonah@ripplecraft.com
      </li>
      <li class="contacts__item">
        <svg class="contacts__icon" viewBox="0 0 16 16"><circle cx="8" cy="8" r="6.5" fill="none" stroke="var(--lime)" stroke-width="1.6"/><ellipse cx="8" cy="8" rx="2.8" ry="6.5" fill="none" stroke="var(--lime)" stroke-width="1.2"/><line x1="1.5" y1="8" x2="14.5" y2="8" stroke="var(--lime)" stroke-width="1.2"/></svg>
        www.ripplecraft.com
      </li>
    </ul>
  </article>
</main>
</body>
</html>
```